Wholesale in Gold Jewellery & Gold Bullion

We are an established gold jewellery and gold bullion wholesaler selling these products to international clients. We already have a name and logo of our company, hence please view attached current card design. We need a completely new design to compliment our business and industry and the final design should be new and elegant.

Contact Information for Business Card

New card details must be same as per current card. Like logo, name, tel no. & etc.

Colors

Designer to choose colors to be used in the design.

```html
<!DOCTYPE html>
<html lang="en">
<head>
<meta charset="utf-8">
<title>Arundel &amp; Co – Business Card</title>
<link rel="stylesheet" href="https://fonts.googleapis.com/css2?family=Cinzel:wght@500;600&family=Open+Sans:wght@400;600;700&display=swap">
<style>
  :root {
    --backdrop: #ece8e1;
    --gold: #d9960f;
    --paper: #ffffff;
    --ink: #333333;
    --on-gold: #ffffff;
    --card-shadow: 0 4px 10px rgba(0,0,0,0.25);
  }
  * { box-sizing: border-box; margin: 0; padding: 0; }
  html, body {
    width: 1200px; height: 900px; overflow: hidden;
    background: var(--backdrop);
  }
  .canvas { position: relative; width: 1200px; height: 900px; }

  .card {
    position: absolute;
    width: 558px; height: 343px;
    box-shadow: var(--card-shadow);
  }

  /* Contact side */
  .card--contact {
    left: 329px; top: 90px;
    background: var(--gold);
    color: var(--on-gold);
    font-family: "Open Sans", Arial, sans-serif;
    text-align: center;
  }
  .holder-name {
    position: absolute; left: 0; right: 0; top: 68px;
    font-family: "Cinzel", "Times New Roman", serif;
    font-weight: 600; font-size: 21px; letter-spacing: 0.5px;
  }
  .holder-role {
    position: absolute; left: 0; right: 0; top: 93px;
    font-size: 15px;
  }
  .rule {
    position: absolute; left: 205px; width: 146px; height: 1px;
    background: var(--on-gold);
  }
  .rule--upper { top: 122px; }
  .rule--lower { top: 183px; }
  .address {
    position: absolute; left: 0; right: 0; top: 131px;
    font-size: 16px; line-height: 20px; font-style: normal;
  }
  .contact-list {
    position: absolute; left: 0; right: 0; top: 192px;
    list-style: none; font-size: 16px; line-height: 20px;
  }
  .contact-list b { font-weight: 700; }

  /* Brand side */
  .card--brand {
    left: 329px; top: 469px;
    background: var(--paper);
  }
  .brand-mark {
    position: absolute; left: 219px; top: 76px;
    width: 120px; height: 120px;
  }
  .brand-name {
    position: absolute; left: 0; right: 0; top: 212px;
    text-align: center;
    font-family: "Cinzel", "Times New Roman", serif;
    font-weight: 500; font-size: 38px; letter-spacing: 0.5px;
    color: var(--ink);
  }
</style>
</head>
<body>
<main class="canvas">
  <section class="card card--contact" aria-label="Business card, contact side">
    <h1 class="holder-name">RAVINDRA KESAVAN</h1>
    <p class="holder-role">Director</p>
    <span class="rule rule--upper"></span>
    <address class="address">12 Harlow Lane,<br>Singapore 208815</address>
    <span class="rule rule--lower"></span>
    <ul class="contact-list">
      <li><b>P:</b> +65 6100 2400</li>
      <li><b>M:</b> +65 9100 5532</li>
      <li><b>F:</b> +65 6100 2411</li>
      <li><b>E:</b> ravindra@arundelco.com</li>
    </ul>
  </section>

  <section class="card card--brand" aria-label="Business card, brand side">
    <svg class="brand-mark" viewBox="0 0 120 120" aria-hidden="true">
      <circle cx="60" cy="60" r="60" fill="var(--gold)"/>
    </svg>
    <p class="brand-name">ARUNDEL &amp; CO</p>
  </section>
</main>
</body>
</html>
```